Letterhead Design Project

Please do not submit designs until I upload file-

Project Deadline Extended

Requirements
Must have
• clean lines and font- easy to read; consistent with the design on the business card
Does not use too much of the real estate of the size of the paper

```html
<!DOCTYPE html>
<html lang="en">
<head>
<meta charset="utf-8">
<title>The Alder Ridge Foundation — Letterhead</title>
<link rel="stylesheet" href="https://fonts.googleapis.com/css2?family=Montserrat:wght@400;500;700&display=swap">
<style>
  :root {
    --backdrop: #ececec;
    --paper: #ffffff;
    --navy: #1f3f6e;
    --ink: #4a4a4a;
    --icon: #6b6b6b;
    --shadow: rgba(0, 0, 0, 0.12);
  }
  * { box-sizing: border-box; margin: 0; padding: 0; }
  html, body {
    width: 1200px;
    height: 795px;
    overflow: hidden;
    background: var(--backdrop);
    font-family: "Montserrat", Arial, sans-serif;
  }
  .letterhead {
    position: absolute;
    left: 340px;
    top: 30px;
    width: 520px;
    height: 735px;
    background: var(--paper);
    box-shadow: 0 4px 18px var(--shadow);
  }
  .brand {
    position: absolute;
    left: 40px;
    top: 44px;
    display: flex;
    align-items: center;
    gap: 8px;
  }
  .brand-mark {
    width: 16px;
    height: 16px;
    background: var(--navy);
    flex: none;
  }
  .brand-name {
    font-weight: 700;
    font-size: 9px;
    line-height: 1.05;
    letter-spacing: 0.04em;
    text-transform: uppercase;
    color: var(--navy);
  }
  .brand-tagline {
    display: block;
    margin-top: 3px;
    font-weight: 400;
    font-size: 4.5px;
    letter-spacing: 0.06em;
    text-transform: uppercase;
    color: var(--ink);
  }
  .contact {
    position: absolute;
    right: 40px;
    top: 38px;
    font-size: 5.5px;
    line-height: 1.9;
    letter-spacing: 0.12em;
    color: var(--ink);
  }
  .contact-address { margin-bottom: 4px; }
  .contact-line {
    display: flex;
    align-items: center;
    gap: 6px;
  }
  .contact-line svg {
    width: 6px;
    height: 6px;
    flex: none;
    fill: none;
    stroke: var(--icon);
    stroke-width: 1.2;
  }
</style>
</head>
<body>
  <main class="letterhead">
    <header class="brand">
      <span class="brand-mark"></span>
      <div class="brand-name">
        The Alder Ridge<br>Foundation
        <span class="brand-tagline">Supporting communities since 1998</span>
      </div>
    </header>

    <address class="contact" style="font-style: normal;">
      <div class="contact-address">
        4120 Harbor Point Drive, Suite 310<br>
        Cedar Bay, FL 33912
      </div>
      <div class="contact-line">
        <svg viewBox="0 0 10 10" aria-hidden="true"><rect x="2.5" y="0.8" width="5" height="8.4" rx="1"/></svg>
        <span>+1 555 014 2280</span>
      </div>
      <div class="contact-line">
        <svg viewBox="0 0 10 10" aria-hidden="true"><rect x="0.8" y="2" width="8.4" height="6" /><path d="M0.8 2 L5 5.5 L9.2 2"/></svg>
        <span>dana.hale@alderridgefoundation.org</span>
      </div>
      <div class="contact-line">
        <svg viewBox="0 0 10 10" aria-hidden="true"><circle cx="5" cy="5" r="4.2"/><path d="M0.8 5 H9.2 M5 0.8 C2.5 3.5 2.5 6.5 5 9.2 M5 0.8 C7.5 3.5 7.5 6.5 5 9.2"/></svg>
        <span>www.alderridgefoundation.org</span>
      </div>
    </address>
  </main>
</body>
</html>
```